Business Cards for a law firm

Business cards for our law firm. Use our silhoette logo and OAK PARTNERS - check our website (www.oakpartners.example)

Contact Information for Business Card

our silhouette logo, OAK PARTNERS, 800-555-0147, Dorian Pemberton, dorian@oakpartners.example

Requirements
Must have
• our silhouette logo, OAK PARTNERS, 800-555-0147, Dorian Pemberton, dorian@oakpartners.example

```html
<!DOCTYPE html>
<html lang="en">
<head>
<meta charset="utf-8">
<title>Oak Partners — Business Card</title>
<link href="https://fonts.googleapis.com/css2?family=Montserrat:wght@400;500;700&family=Tenor+Sans&display=swap" rel="stylesheet">
<style>
  :root {
    --navy: #243369;
    --paper: #ffffff;
    --backdrop: #e1e6e8;
  }
  * { box-sizing: border-box; margin: 0; padding: 0; }
  html, body { width: 1200px; height: 960px; overflow: hidden; }
  body { background: var(--backdrop); position: relative; font-family: "Montserrat", sans-serif; color: var(--navy); }

  .card {
    position: absolute;
    top: 105px;
    width: 429px;
    height: 751px;
    border-radius: 26px;
    background: var(--navy);
  }
  .card--front { left: 143px; }
  .card--back { left: 631px; }
  .card__face {
    position: absolute;
    inset: 0 0 0 15px;
    border-radius: 26px;
    background: var(--paper);
  }

  .wordmark { font-family: "Tenor Sans", sans-serif; font-weight: 400; color: var(--navy); }

  .front__wordmark {
    position: absolute;
    left: 213px;
    top: 326px;
    font-size: 50px;
    letter-spacing: 2px;
    white-space: nowrap;
    transform: translate(-50%, -50%) rotate(-90deg);
  }
  .front__mark {
    position: absolute;
    left: 178px;
    top: 578px;
    width: 72px;
    height: 72px;
    background: var(--navy);
  }

  .back__brand {
    position: absolute;
    left: 85px;
    top: 52px;
    display: flex;
    align-items: center;
    gap: 12px;
  }
  .back__mark { width: 56px; height: 56px; background: var(--navy); }
  .back__wordmark { font-size: 28px; line-height: 0.95; letter-spacing: 0.5px; }

  .person {
    position: absolute;
    left: 42px;
    top: 560px;
    font-size: 30px;
    letter-spacing: 0.5px;
    white-space: nowrap;
  }
  .person__first { font-weight: 700; }
  .person__last { font-weight: 400; }

  .contact {
    position: absolute;
    left: 42px;
    top: 616px;
    list-style: none;
  }
  .contact__item { display: flex; align-items: center; gap: 10px; height: 25px; white-space: nowrap; font-size: 15px; letter-spacing: 0.6px; }
  .contact__item--phone { font-size: 19px; height: 27px; }
  .contact__icon { width: 18px; height: 18px; flex: none; }
</style>
</head>
<body>
  <div class="card card--front">
    <div class="card__face">
      <span class="wordmark front__wordmark">OAK PARTNERS</span>
      <div class="front__mark" aria-hidden="true"></div>
    </div>
  </div>

  <div class="card card--back">
    <div class="card__face">
      <div class="back__brand">
        <div class="back__mark" aria-hidden="true"></div>
        <div class="wordmark back__wordmark">OAK<br>PARTNERS</div>
      </div>

      <p class="person"><span class="person__first">DORIAN</span> <span class="person__last">PEMBERTON</span></p>

      <ul class="contact">
        <li class="contact__item contact__item--phone">
          <svg class="contact__icon" viewBox="0 0 24 24" fill="var(--navy)" aria-hidden="true"><path d="M6.6 10.8c1.4 2.8 3.8 5.1 6.6 6.6l2.2-2.2c.3-.3.7-.4 1-.2 1.1.4 2.3.6 3.6.6.6 0 1 .4 1 1V20c0 .6-.4 1-1 1C10.6 21 3 13.4 3 4c0-.6.4-1 1-1h3.5c.6 0 1 .4 1 1 0 1.3.2 2.5.6 3.6.1.3 0 .7-.2 1L6.6 10.8z"/></svg>
          <span>800-555-0147</span>
        </li>
        <li class="contact__item">
          <svg class="contact__icon" viewBox="0 0 24 24" fill="none" stroke="var(--navy)" stroke-width="2" aria-hidden="true"><circle cx="12" cy="12" r="9"/><path d="M3 12h18M12 3c3 3 3 15 0 18M12 3c-3 3-3 15 0 18"/></svg>
          <span>WWW.OAKPARTNERS.EXAMPLE</span>
        </li>
        <li class="contact__item">
          <svg class="contact__icon" viewBox="0 0 24 24" fill="none" stroke="var(--navy)" stroke-width="2" aria-hidden="true"><rect x="3" y="6" width="18" height="13"/><path d="M3 6l9 7 9-7"/></svg>
          <span>DORIAN@OAKPARTNERS.EXAMPLE</span>
        </li>
      </ul>
    </div>
  </div>
</body>
</html>
```